Maplecrest Disability - Social Security Disability Attorneys

Our company is expanding to attract clients nationwide for our social security disability practice. We have a logo, but I am looking for a creative and elegant letterhead that projects an image of being technologically advanced but still professional enough for the legal field. I am looking for the "wow factor" combined with this is still professional enough for a law practice.

Requesting letterhead and business card design
Updates

Had to update and change the logo. The previous logo had a typo. Please send updates with the new logo for consideration. The letterhead and business cards should be professional enough to be used for a law firm. Thanks.

Industry/Entity Type

Law Practice, Law Firm, Healthcare Industry, Government

Colors

Designer to choose colors to be used in the design.

Requirements
Nice to have
• **Please create a vertical design for the business card**

```html
<!DOCTYPE html>
<html lang="en">
<head>
<meta charset="utf-8">
<title>Maplecrest Disability – Letterhead</title>
<link rel="stylesheet" href="https://fonts.googleapis.com/css2?family=Tinos&family=Open+Sans:wght@400;700&display=swap">
<style>
  :root {
    --backdrop: #d9dadd;
    --paper: #ffffff;
    --navy: #2b3f8f;
    --ink: #1c1c1c;
    --footer-ink: #333333;
    --rule: #555555;
    --signature-tint: #e3e7f4;
  }
  * { margin: 0; padding: 0; box-sizing: border-box; }
  html, body {
    width: 1200px; height: 900px; overflow: hidden;
    background: var(--backdrop);
  }
  .canvas { position: relative; width: 1200px; height: 900px; }
  .letterhead {
    position: absolute; left: 270px; top: 22px;
    width: 660px; height: 856px;
    background: var(--paper);
    box-shadow: 0 4px 18px rgba(0,0,0,0.18);
    font-family: "Tinos", "Times New Roman", serif;
    color: var(--ink);
  }
  .brand-name {
    position: absolute; left: 0; top: 78px; width: 440px;
    text-align: center;
    font-family: "Tinos", "Times New Roman", serif; font-weight: 400;
    font-size: 19px; color: var(--navy);
  }
  .recipient {
    position: absolute; left: 104px; top: 166px;
    display: flex; gap: 20px; font-size: 11px; line-height: 13px;
  }
  .letter-body {
    position: absolute; left: 100px; top: 230px; width: 450px;
    font-size: 11px; line-height: 12.4px;
  }
  .letter-body p { margin-bottom: 12px; }
  .letter-body .salutation { margin-bottom: 10px; }
  .closing { margin-top: 14px; margin-bottom: 4px !important; }
  .signature {
    display: block; width: 150px; height: 34px;
    background: var(--signature-tint); border-radius: 3px;
  }
  .contact {
    position: absolute; right: 96px; top: 764px;
    text-align: right;
    font-family: "Open Sans", Arial, sans-serif; font-size: 7.5px;
    line-height: 13px; color: var(--footer-ink); letter-spacing: 0.2px;
  }
  .contact b { font-weight: 700; }
  .contact-rule {
    position: absolute; left: 572px; top: 762px;
    width: 1px; height: 94px; background: var(--rule);
  }
</style>
</head>
<body>
<main class="canvas">
  <article class="letterhead">
    <header class="brand-name">Maplecrest Disability</header>

    <section class="recipient">
      <div>To:</div>
      <div>Mr./Mrs. Customerand Partner<br>100 Good Avenue<br>New York<br>NY 55254</div>
    </section>

    <section class="letter-body">
      <p class="salutation">Dear Customer,</p>
      <p>Lorem ipsum dolor sit amet, consetetur sadipscing elitr, sed diam nonumy eirmod tempor invidunt ut labore et dolore magna aliquyam erat, sed diam voluptua. At vero eos et accusam et justo duo dolores et ea rebum. Stet clita kasd gubergren, no sea takimata sanctus est Lorem ipsum dolor sit amet. Lorem ipsum dolor sit amet, consetetur sadipscing elitr, sed diam nonumy eirmod tempor invidunt ut labore et dolore magna aliquyam erat, sed diam voluptua. At vero eos et accusam et justo duo dolores et ea rebum. Stet clita kasd gubergren, no sea takimata sanctus est Lorem ipsum dolor sit amet. Lorem ipsum dolor sit amet, consetetur sadipscing elitr, sed diam nonumy eirmod tempor invidunt ut labore et dolore magna aliquyam erat, sed diam voluptua. At vero eos et accusam et justo duo dolores et ea rebum. Stet clita kasd gubergren, no sea takimata sanctus est Lorem ipsum dolor sit amet.</p>
      <p>Duis autem vel eum iriure dolor in hendrerit in vulputate velit esse molestie consequat, vel illum dolore eu feugiat nulla facilisis at vero eros et accumsan et iusto odio dignissim qui blandit praesent luptatum zzril delenit augue duis dolore te feugait nulla facilisi. Lorem ipsum dolor sit amet, consectetuer adipiscing elit, sed diam nonummy nibh euismod tincidunt ut laoreet dolore magna aliquam erat volutpat.</p>
      <p>Nam liber tempor cum soluta nobis eleifend option congue nihil imperdiet doming id quod mazim placerat facer possim assum. Lorem ipsum dolor sit amet, consectetuer adipiscing elit, sed diam nonummy nibh euismod tincidunt ut laoreet dolore magna aliquam erat volutpat. Ut wisi enim ad minim veniam, quis nostrud exerci tation ullamcorper suscipit lobortis nisl ut aliquip ex ea commodo consequat.</p>
      <p class="closing">Sincerely,</p>
      <span class="signature" role="img" aria-label="Handwritten signature of the sending attorney"></span>
    </section>

    <footer class="contact">
      1420 RIDGEVIEW PLACE<br>
      ATLANTA, GA 30309<br>
      <b>P:</b> 404-555-0140<br>
      <b>F:</b> 404-555-0147
    </footer>
    <div class="contact-rule"></div>
  </article>
</main>
</body>
</html>
```